Web Developer Needs a Business Card Design

I need a personal business card design that represents me as a web developer for potential employers. I would like the background to be a dark color on the front for contrast with my logo and name. The back will have all my information along with a smaller version of the logo. I want something with a modern look and feel, not too conservative. This will be used for potential employers and freelance work.

Industry/Entity Type

Business

Contact Information for Business Card

Front should have my logo and name. The back should have all my personal information which would include: name: Tom Varulek, phone: 570-614-3098, email: tomvarulek@quillbox.net, website url: www.tomvarulek.net, logo, web developer.

Font styles to use
Sans Serif

Requirements
Must have
• Must include my logo. The color palette base color will be the logo color.

```html
<!DOCTYPE html>
<html lang="en">
<head>
<meta charset="utf-8">
<title>Tom Varulek — Business Card</title>
<link rel="stylesheet" href="https://fonts.googleapis.com/css2?family=Open+Sans:wght@400;600;700&display=swap">
<style>
  :root {
    --teal: #6fcab5;
    --teal-deep: #2d6f62;
    --night: #16302b;
    --ink: #111111;
    --paper: #f7f7f6;
    --white: #ffffff;
    --backdrop: #d9d9d7;
  }
  * { box-sizing: border-box; margin: 0; padding: 0; }
  html, body { width: 1200px; height: 864px; overflow: hidden; }
  body {
    background: var(--backdrop);
    font-family: "Open Sans", sans-serif;
    display: flex;
    align-items: center;
    justify-content: center;
    gap: 40px;
  }
  .card {
    position: relative;
    width: 560px;
    height: 320px;
    overflow: hidden;
    box-shadow: 0 6px 18px rgba(0,0,0,0.18);
  }

  /* Contact side */
  .card-info { background: var(--paper); }
  .brand {
    display: flex;
    align-items: center;
    gap: 10px;
  }
  .brand-dot {
    width: 22px; height: 22px;
    border-radius: 50%;
    background: var(--teal);
    flex: none;
  }
  .brand-name {
    color: var(--teal);
    font-size: 26px;
    font-weight: 600;
    letter-spacing: 0.5px;
    line-height: 1;
  }
  .card-info .brand {
    position: absolute;
    top: 50px;
    left: 0;
    width: 100%;
    justify-content: center;
    padding-left: 40px;
  }
  .identity {
    position: absolute;
    top: 118px;
    right: 308px;
    display: flex;
    flex-direction: column;
    align-items: flex-end;
  }
  .identity-name {
    color: var(--teal);
    font-size: 30px;
    font-weight: 400;
    line-height: 1.15;
    white-space: nowrap;
  }
  .identity-role {
    color: var(--ink);
    font-size: 16px;
    font-weight: 400;
    letter-spacing: 1px;
    line-height: 1.2;
  }
  .divider {
    position: absolute;
    left: 266px;
    top: 120px;
    width: 1px;
    height: 88px;
    background: var(--ink);
  }
  .contacts {
    position: absolute;
    left: 284px;
    top: 118px;
    list-style: none;
  }
  .contact {
    display: flex;
    align-items: center;
    gap: 10px;
    font-size: 16px;
    color: var(--ink);
    line-height: 29px;
    letter-spacing: 0.3px;
    white-space: nowrap;
  }
  .contact-icon { width: 14px; height: 14px; flex: none; }
  .stripe-rule {
    position: absolute; left: 0; width: 100%;
    height: 4px; background: var(--ink);
  }
  .stripe-rule.top { top: 218px; }
  .stripe-rule.bottom { top: 280px; }
  .stripe-band {
    position: absolute; left: 0; top: 222px;
    width: 100%; height: 58px;
    background: var(--teal);
  }

  /* Name side */
  .card-front { background: var(--night); }
  .front-fill {
    position: absolute; inset: 0;
    background: radial-gradient(circle at 50% 50%, var(--teal-deep) 0%, var(--night) 75%);
  }
  .front-content {
    position: absolute; inset: 0;
    display: flex;
    flex-direction: column;
    align-items: center;
    justify-content: center;
    gap: 22px;
  }
  .front-name {
    font-size: 44px;
    font-weight: 700;
    color: var(--white);
    letter-spacing: 1px;
    line-height: 1.1;
    white-space: nowrap;
  }
</style>
</head>
<body>

  <section class="card card-info" aria-label="Business card, contact side">
    <div class="brand">
      <span class="brand-dot"></span>
      <span class="brand-name">varulek</span>
    </div>

    <div class="identity">
      <span class="identity-name">Tom Varulek</span>
      <span class="identity-role">web developer</span>
    </div>

    <div class="divider"></div>

    <ul class="contacts">
      <li class="contact">
        <svg class="contact-icon" viewBox="0 0 14 14" aria-hidden="true">
          <rect width="14" height="14" rx="2" fill="var(--teal)"/>
          <path d="M4 3.2 L5.6 3 L6.3 5 L5.3 5.8 Q6.2 7.8 8.2 8.7 L9 7.7 L11 8.4 L10.8 10 Q7 10.4 4.8 8 Q3.2 5.8 4 3.2 Z" fill="#fff"/>
        </svg>
        570-614-3098
      </li>
      <li class="contact">
        <svg class="contact-icon" viewBox="0 0 14 14" aria-hidden="true">
          <rect width="14" height="14" rx="2" fill="var(--teal)"/>
          <circle cx="7" cy="7" r="4" fill="none" stroke="#fff" stroke-width="1.2"/>
          <path d="M3 7 H11 M7 3 Q4.8 7 7 11 M7 3 Q9.2 7 7 11" fill="none" stroke="#fff" stroke-width="1"/>
        </svg>
        www.tomvarulek.net
      </li>
      <li class="contact">
        <svg class="contact-icon" viewBox="0 0 14 14" aria-hidden="true">
          <rect width="14" height="14" rx="2" fill="var(--teal)"/>
          <rect x="3" y="4.2" width="8" height="5.6" fill="none" stroke="#fff" stroke-width="1.1"/>
          <path d="M3 4.2 L7 7.4 L11 4.2" fill="none" stroke="#fff" stroke-width="1.1"/>
        </svg>
        tomvarulek@quillbox.net
      </li>
    </ul>

    <div class="stripe-rule top"></div>
    <div class="stripe-band"></div>
    <div class="stripe-rule bottom"></div>
  </section>

  <section class="card card-front" aria-label="Business card, name side">
    <div class="front-fill" role="img" aria-label="Repeating pattern of the teal brand mark across the card"></div>
    <div class="front-content">
      <div class="brand">
        <span class="brand-dot"></span>
        <span class="brand-name">varulek</span>
      </div>
      <div class="front-name">Tom Varulek</div>
    </div>
  </section>

</body>
</html>
```